Kellwyn Surface Records

I have a current web site that it looking quite aged and it needs a new lease of life. This is a Graffiti Management Website so is all about data processing and management of information. I want a html 5 view on any platform design. clean crisp and new. I have provided some screen shots of my current site.

Target Market(s)

The Target Market will be local government. most users will not be heavy pc users

Industry/Entity Type

Management

Font styles to use
Sans Serif
Other font styles liked:
• web font like calibri

Colors

Designer to choose colors to be used in the design.

Requirements
Must have
• Must have menus similar to attachments

```html
<!DOCTYPE html>
<html lang="en">
<head>
<meta charset="utf-8">
<title>Kellwyn Surface Records</title>
<link rel="stylesheet" href="https://fonts.googleapis.com/css2?family=Roboto:wght@300;400;500;700&family=Oswald:wght@400&display=swap">
<style>
:root{
  --pink:#f1566a;
  --white:#ffffff;
  --ink:#333338;
  --muted:#6d6d72;
  --line:#e3e3e6;
  --slate:#4a4a50;
  --footer:#2f2f33;
  --bar:#d9d9dc;
  --placeholder:#c9cdd2;
}
*{box-sizing:border-box;margin:0;padding:0}
html,body{width:1200px;height:3333px;overflow:hidden}
body{font-family:"Roboto",Arial,sans-serif;color:var(--ink);background:var(--white)}
a{color:inherit;text-decoration:none}

/* header */
.site-header{height:145px;background:var(--pink);color:var(--white);position:relative}
.brand{position:absolute;left:0;right:0;top:6px;text-align:center}
.brand-name{font-size:46px;font-weight:400;letter-spacing:22px;padding-left:22px;line-height:54px}
.brand-sub{font-size:17px;font-weight:500;letter-spacing:1px;margin-top:2px}
.account-links{position:absolute;right:90px;top:20px;font-size:14px;font-weight:500;display:flex;gap:30px}
.account-links span{border-left:1px solid rgba(255,255,255,.6);padding-left:14px}
.main-nav{position:absolute;left:110px;right:110px;bottom:0;height:36px;display:flex;justify-content:space-between;border-top:1px solid rgba(255,255,255,.35);font-size:14px;font-weight:500}
.main-nav a{padding:9px 18px 0}
.main-nav a.active{border-bottom:3px solid var(--white)}

/* hero */
.hero{height:585px;position:relative;overflow:hidden}
.hero-bg{position:absolute;inset:0;background:linear-gradient(120deg,#2b2b2e 0%,#55545a 40%,#3a393d 70%,#232325 100%)}
.hero-copy{position:absolute;left:117px;top:170px;color:var(--white);width:640px}
.hero-copy h1{font-size:44px;font-weight:400;line-height:48px;letter-spacing:.5px}
.hero-copy p{font-size:19px;line-height:26px;margin-top:18px;font-weight:300}
.btn-hero{display:inline-block;margin-top:18px;background:var(--pink);color:var(--white);font-size:16px;padding:17px 40px;letter-spacing:.5px}
.hero-art{position:absolute;width:130px;height:130px;border-radius:50%;border:3px solid rgba(255,255,255,.8)}
.art-1{left:728px;top:120px;background:radial-gradient(circle,#c06a3c,#5a2b1c)}
.art-2{left:917px;top:120px;background:radial-gradient(circle,#b9b6c4,#564f66)}
.art-3{left:728px;top:312px;background:radial-gradient(circle,#4d6fc9,#1d2a6a)}
.art-4{left:917px;top:312px;background:radial-gradient(circle,#a79a8c,#4b3c3a)}
.slider-dots{position:absolute;right:82px;bottom:66px;display:flex;gap:6px}
.slider-dots i{width:10px;height:10px;border-radius:50%;background:#8a8a8f}
.slider-dots i.on{background:var(--pink)}

/* products */
.products{height:459px;background:var(--pink);color:var(--white);padding:30px 83px 0}
.section-title{font-size:30px;font-weight:400;text-align:center;letter-spacing:1px}
.product-grid{display:grid;grid-template-columns:repeat(6,1fr);gap:14px;margin-top:14px}
.product-tab{font-size:13px;font-weight:500;text-align:center;border-top:1px solid rgba(255,255,255,.45);border-bottom:1px solid rgba(255,255,255,.45);height:50px;display:flex;align-items:center;justify-content:center;line-height:15px}
.product-icon{height:110px;display:flex;align-items:center;justify-content:center}
.product-text{font-size:13px;line-height:19px;height:57px;overflow:hidden;padding:0 6px}
.btn-outline{display:block;margin:29px auto 0;width:135px;height:38px;border:1px solid rgba(255,255,255,.85);text-align:center;line-height:36px;font-size:13px}

/* about + report */
.info{height:525px;display:flex;padding:0 75px 0 97px}
.info-col{flex:1;padding-top:48px}
.info-col.about{padding-right:42px;border-right:1px solid var(--line)}
.info-col.report{padding-left:41px}
.info h2{font-size:30px;font-weight:400;color:#2a2a2e;letter-spacing:.5px;padding-bottom:18px;border-bottom:1px solid var(--line)}
.about-list{list-style:none;margin-top:22px}
.about-list li{font-size:13px;line-height:18px;margin-bottom:16px;color:var(--muted)}
.hl{color:var(--pink)}
.more-link{display:flex;align-items:center;gap:12px;font-size:13px;margin-top:22px;color:var(--ink)}
.more-link i{width:20px;height:20px;border-radius:50%;background:var(--pink)}
.report-intro{font-size:13px;line-height:19px;color:var(--muted);margin-top:22px}
.stat{display:flex;align-items:flex-end;margin-top:22px}
.stat-body{flex:1}
.stat-label{font-size:13px;color:var(--muted)}
.stat-bar{height:6px;background:var(--bar);margin-top:8px}
.stat-bar b{display:block;height:100%;background:var(--pink)}
.stat-value{font-family:"Oswald",Arial,sans-serif;font-size:36px;width:120px;text-align:center;line-height:40px;color:#2a2a2e}
.stat-trend{width:55px;font-size:11px;color:#999;line-height:14px}
.stat-trend span{color:var(--pink)}
.report .more-link{margin-top:38px}

/* benefits */
.benefits{height:453px;background:var(--slate);color:var(--white);padding:42px 80px 0 78px}
.benefits .section-title{text-align:left;font-size:30px}
.benefit-grid{display:grid;grid-template-columns:repeat(4,1fr);gap:19px;margin-top:22px}
.benefit-photo{height:137px}
.bp-1{background:linear-gradient(135deg,#cfe2ee,#9bbccf)}
.bp-2{background:linear-gradient(135deg,#6d5a47,#2e2620)}
.bp-3{background:linear-gradient(135deg,#b77b45,#3c2414)}
.bp-4{background:linear-gradient(135deg,#2b86c9,#0d3a72)}
.benefit h3{font-size:14px;font-weight:500;text-align:center;margin-top:24px;letter-spacing:.3px}
.benefit p{font-size:13px;line-height:18px;text-align:center;margin-top:10px;height:54px;overflow:hidden;color:#e6e6e8}
.benefit .btn-outline{margin-top:22px;width:165px;height:38px;border-color:rgba(255,255,255,.5)}

/* legislation */
.legislation{height:472px;padding-top:20px}
.legis-icon{display:block;margin:0 auto}
.legislation .section-title{color:#2a2a2e;margin-top:32px}
.legis-grid{display:grid;grid-template-columns:498px 503px;gap:20px 19px;margin:40px 0 0 83px}
.legis-item{height:91px;border:1px solid #f4a7b0;display:flex;align-items:center;justify-content:center;font-size:13px;font-weight:500;color:#444;letter-spacing:.3px}

/* help */
.help{height:181px;background:var(--slate);color:var(--white);padding-top:30px}
.help .section-title{font-size:28px;font-weight:700}
.contact-row{display:flex;justify-content:space-between;padding:36px 95px 0 86px}
.contact{display:flex;align-items:center;gap:18px;font-size:15px;line-height:20px}

/* location placeholder */
.map{height:375px;background:var(--placeholder)}

/* footer */
.site-footer{height:138px;background:var(--footer);color:var(--white);position:relative}
.foot-brand{position:absolute;left:97px;top:30px}
.foot-brand .brand-name{font-size:30px;letter-spacing:14px;padding-left:0;line-height:34px}
.foot-brand .brand-sub{font-size:11px;letter-spacing:1px;margin-top:2px}
.copyright{font-size:11px;margin-top:14px;color:#c8c8cc}
.social{position:absolute;right:100px;top:58px;display:flex;gap:10px}
.social i{width:30px;height:30px;border-radius:50%;border:1px solid #bdbdc2}
.to-top{position:absolute;right:12px;top:56px}
</style>
</head>
<body>

<header class="site-header">
  <div class="brand">
    <div class="brand-name">KWSR</div>
    <div class="brand-sub">KELLWYN SURFACE RECORDS</div>
  </div>
  <div class="account-links"><a href="#">LOGIN</a><span>DEMO LOGIN</span></div>
  <nav class="main-nav">
    <a href="#" class="active">HOME</a>
    <a href="#">PRODUCTS</a>
    <a href="#">REPORTS</a>
    <a href="#">BENEFITS</a>
    <a href="#">LEGISLATION</a>
    <a href="#">CONTACT US</a>
  </nav>
</header>

<section class="hero">
  <div class="hero-bg" role="img" aria-label="Blurred photograph of a graffiti covered wall"></div>
  <div class="hero-copy">
    <h1>HELPING YOU CLEAN UP<br>YOUR COMMUNITY</h1>
    <p>KWSR is an Online Database System to Manage Graffiti in<br>your area or Your Properties</p>
    <a href="#" class="btn-hero">READ MORE</a>
  </div>
  <div class="hero-art art-1" role="img" aria-label="Round photo of a colourful graffiti mural"></div>
  <div class="hero-art art-2" role="img" aria-label="Round photo of tagged panels"></div>
  <div class="hero-art art-3" role="img" aria-label="Round photo of a blue painted wall"></div>
  <div class="hero-art art-4" role="img" aria-label="Round photo of graffiti on a fence"></div>
  <div class="slider-dots"><i class="on"></i><i></i><i></i></div>
</section>

<section class="products">
  <h2 class="section-title">PRODUCTS</h2>
  <div class="product-grid">
    <div class="product">
      <div class="product-tab">GRAFFITI REGISTER</div>
      <div class="product-icon"><svg width="40" height="52" viewBox="0 0 40 52" fill="none" stroke="#fff" stroke-width="3"><rect x="10" y="18" width="20" height="32" rx="3" fill="#fff"/><rect x="15" y="10" width="10" height="8"/><line x1="20" y1="4" x2="20" y2="10"/><circle cx="31" cy="5" r="1.5" fill="#fff"/><circle cx="35" cy="10" r="1.5" fill="#fff"/></svg></div>
      <p class="product-text">KWSR provides a National Register of Graffiti...</p>
      <a href="#" class="btn-outline">More</a>
    </div>
    <div class="product">
      <div class="product-tab">GRAFFITI PHOTOS</div>
      <div class="product-icon"><svg width="50" height="42" viewBox="0 0 50 42" fill="none" stroke="#fff" stroke-width="3"><rect x="2" y="2" width="46" height="38" rx="3"/><polyline points="6,34 18,20 28,30 34,24 44,34"/><circle cx="35" cy="12" r="4"/></svg></div>
      <p class="product-text">KWSR allows its subscribers to add Photos to Jobs...</p>
      <a href="#" class="btn-outline">More</a>
    </div>
    <div class="product">
      <div class="product-tab">GRAFFITI ARCHIVE</div>
      <div class="product-icon"><svg width="40" height="50" viewBox="0 0 40 50" fill="none" stroke="#fff" stroke-width="3"><path d="M4 2h22l10 10v36H4z"/><path d="M26 2v10h10"/><rect x="14" y="22" width="12" height="16"/></svg></div>
      <p class="product-text">KWSR will hold secure the sensitive details of Jobs...</p>
      <a href="#" class="btn-outline">More</a>
    </div>
    <div class="product">
      <div class="product-tab">SEARCHABLE DATABASE</div>
      <div class="product-icon"><svg width="52" height="44" viewBox="0 0 52 44" fill="none" stroke="#fff" stroke-width="3"><path d="M2 8h16l4 5h22v27H2z"/><circle cx="32" cy="27" r="7"/><line x1="37" y1="32" x2="44" y2="39"/></svg></div>
      <p class="product-text">KWSR allows you to search your own records...</p>
      <a href="#" class="btn-outline">More</a>
    </div>
    <div class="product">
      <div class="product-tab">STATISTICAL ANALYSIS REPORTS</div>
      <div class="product-icon"><svg width="48" height="44" viewBox="0 0 48 44" fill="none" stroke="#fff" stroke-width="3"><polyline points="4,2 4,40 46,40"/><polyline points="10,32 20,20 28,26 42,8"/></svg></div>
      <p class="product-text">KWSR lets you run statistical reports for...</p>
      <a href="#" class="btn-outline">More</a>
    </div>
    <div class="product">
      <div class="product-tab">DATA CONVERSION</div>
      <div class="product-icon"><svg width="52" height="40" viewBox="0 0 52 40" fill="none" stroke="#fff" stroke-width="3"><rect x="2" y="4" width="24" height="18" rx="4"/><rect x="24" y="18" width="24" height="18" rx="4"/><polyline points="30,6 36,6 36,12"/><polyline points="20,34 14,34 14,28"/></svg></div>
      <p class="product-text">KWSR can provide a Data Conversion service...</p>
      <a href="#" class="btn-outline">More</a>
    </div>
  </div>
</section>

<section class="info">
  <div class="info-col about">
    <h2>ABOUT US</h2>
    <ul class="about-list">
      <li><span class="hl">KWSR</span> is an Online Database System to Manage Graffiti in your area or Your Properties.</li>
      <li><span class="hl">KWSR</span> allows you to Register, Track, Report and Archive Graffiti Jobs with Photographic Records.</li>
      <li><span class="hl">KWSR</span> records both Estimated and Actual hours and costs for each job, enabling you to track the effectiveness of Anti Graffiti policy.</li>
      <li><span class="hl">KWSR</span> allows sharing of Critical Graffiti Tag and Photographic Data between its subscribers, assisting with tracking down Serial Graffiti Offenders.</li>
      <li><span class="hl">KWSR</span> has a Statistical and Comparison Reporting Systems to allow its subscribers to graphically report and compare their Graffiti Data.</li>
    </ul>
    <a href="#" class="more-link">More <i></i></a>
  </div>
  <div class="info-col report">
    <h2>REPORT</h2>
    <p class="report-intro">Statistical Reports can be done instantaneously and can be run on any data stored with in <span class="hl">KWSR</span>. Charts and Graphs are available to clearly show trends and details for Management Purposes.</p>
    <div class="stat">
      <div class="stat-body"><div class="stat-label">Graffiti type Report (10-10-2014 to 10-12-2014)</div><div class="stat-bar"><b style="width:50.5%"></b></div></div>
      <div class="stat-value">50,5%</div>
      <div class="stat-trend"><span>&#9650;</span><br>+12%</div>
    </div>
    <div class="stat">
      <div class="stat-body"><div class="stat-label">Graffiti type Report (10-10-2014 to 10-12-2014)</div><div class="stat-bar"><b style="width:20%"></b></div></div>
      <div class="stat-value">20%</div>
      <div class="stat-trend"><span>&#9650;</span><br>+8%</div>
    </div>
    <div class="stat">
      <div class="stat-body"><div class="stat-label">Graffiti type Report (10-10-2014 to 10-12-2014)</div><div class="stat-bar"><b style="width:29.5%"></b></div></div>
      <div class="stat-value">29.5%</div>
      <div class="stat-trend"><span>&#9660;</span><br>-4.7%</div>
    </div>
    <a href="#" class="more-link">More <i></i></a>
  </div>
</section>

<section class="benefits">
  <h2 class="section-title">BENEFITS</h2>
  <div class="benefit-grid">
    <div class="benefit">
      <div class="benefit-photo bp-1" role="img" aria-label="Photo of a piggy bank for cost savings"></div>
      <h3>COST EFFECTIVE</h3>
      <p><span class="hl">KWSR</span> allows you to track the cost and effectiveness of your Graffiti Removal. Compare the estimates...</p>
      <a href="#" class="btn-outline">Read more</a>
    </div>
    <div class="benefit">
      <div class="benefit-photo bp-2" role="img" aria-label="Photo of a graffiti artwork on a wall"></div>
      <h3>PHOTOGRAPHIC RECORDS</h3>
      <p>Store any photographic records of New, Existing and Completed Graffiti Jobs. Archive all completed...</p>
      <a href="#" class="btn-outline">Read more</a>
    </div>
    <div class="benefit">
      <div class="benefit-photo bp-3" role="img" aria-label="Photo of a judge's gavel on a desk"></div>
      <h3>ASSIST PROSECUTION</h3>
      <p><span class="hl">KWSR</span> can assist with the possible prosecution of offenders with records of previous tags inside...</p>
      <a href="#" class="btn-outline">Read more</a>
    </div>
    <div class="benefit">
      <div class="benefit-photo bp-4" role="img" aria-label="Photo of a hand touching a digital world map"></div>
      <h3>ACCESS AND SECURITY</h3>
      <p>You can access your data from any PC around the world connected to the Internet. You can give...</p>
      <a href="#" class="btn-outline">Read more</a>
    </div>
  </div>
</section>

<section class="legislation">
  <svg class="legis-icon" width="112" height="112" viewBox="0 0 112 112" fill="none" stroke="#f1566a" stroke-width="3">
    <circle cx="56" cy="56" r="53" stroke-width="2"/>
    <g transform="rotate(-40 56 50)"><rect x="42" y="34" width="28" height="14" rx="2"/><line x1="56" y1="48" x2="56" y2="74"/></g>
    <line x1="40" y1="80" x2="72" y2="80"/>
  </svg>
  <h2 class="section-title">LEGISLATION</h2>
  <div class="legis-grid">
    <a href="#" class="legis-item">NSW GRAFFITI LEGISLATION</a>
    <a href="#" class="legis-item">NSW GOVERNMENT PERSPECTIVE ON GRAFFITI</a>
    <a href="#" class="legis-item">NSW LOCAL GOVERNMENT GRAFFITI AMMENDMENT ACT 2002</a>
    <a href="#" class="legis-item">NSW LOCAL GOVERNMENT LEGISLATION REGARDING GRAFFITI REMOVAL</a>
  </div>
</section>

<section class="help">
  <h2 class="section-title">JUST IN CASE YOU NEED ANY HELP</h2>
  <div class="contact-row">
    <div class="contact">
      <svg width="42" height="36" viewBox="0 0 42 36" fill="#f1566a"><path d="M21 2 2 18h6v16h10V24h6v10h10V18h6z"/></svg>
      <div>Kellwyn Surface Records<br>PO Box 118, Larchmere, NSW 2290</div>
    </div>
    <div class="contact">
      <svg width="30" height="36" viewBox="0 0 30 36" fill="#f1566a"><path d="M6 2h6l3 9-4 3c2 5 5 8 9 10l3-4 7 3v7c0 2-2 4-4 4C13 34 2 22 2 8c0-3 2-6 4-6z"/></svg>
      <div style="font-size:24px">(02) 5550 1234</div>
    </div>
    <div class="contact">
      <svg width="42" height="30" viewBox="0 0 42 30" fill="none" stroke="#f1566a" stroke-width="3"><rect x="2" y="2" width="38" height="26"/><polyline points="2,2 21,17 40,2"/></svg>
      <div>enquiries@kellwyn.example<br>support@kellwyn.example</div>
    </div>
  </div>
</section>

<section class="map" role="img" aria-label="Map showing the office location"></section>

<footer class="site-footer">
  <div class="foot-brand">
    <div class="brand-name">KWSR</div>
    <div class="brand-sub">KELLWYN SURFACE RECORDS</div>
    <div class="copyright">copyright 2014 KWSR all rights reserved</div>
  </div>
  <div class="social"><i></i><i></i><i></i><i></i></div>
  <svg class="to-top" width="34" height="34" viewBox="0 0 34 34"><circle cx="17" cy="17" r="16" fill="#f1566a"/><path d="M17 9v16M10 16l7-7 7 7" stroke="#fff" stroke-width="3" fill="none"/></svg>
</footer>

</body>
</html>
```